Accountability Project Graphics

I want to create 10 social media graphics (new Instagram size 4:5 (1080 x 1350 pixels) focusing on our Quilvo Accountability App, using any of the 3 pictures attached. Use the attached pics only, NO RANDOM STOCK PHOTOGRAPHY. For the color scheme, use the landing page colors/fonts (attached).
You can add any of the 3 photos attached but I mainly need BOLD text that includes these headlines and sub-headlines on them.
Please NOTE for all the headlines below, also add this sub-headline on each graphic:
Stay Consistent with RT in Your Pocket!
Here are the headlines:
• Stop Starting Over Every Monday
• You don't need more willpower. You need more support
• Built for women who are tired of doing this alone
• When Motivation Fades, RT Checks In
• The Support System You've Been Missing
• Support When Motivation Disappears
• What if RT Checked in Every Day?
• The Missing Piece Isn't Another Diet
• Eat the food you love. Stay accountable every day.
• One Bad Meal Doesn't Mean You Failed
women over 40 trying to lose weight

```html
<!DOCTYPE html>
<html lang="en">
<head>
<meta charset="utf-8">
<title>RT Accountability App – Social Graphics</title>
<link rel="stylesheet" href="https://fonts.googleapis.com/css2?family=Roboto+Serif:ital,opsz,wght@0,8..144,800;1,8..144,800&family=Roboto:ital,wght@0,400;1,400&display=swap">
<style>
  :root {
    --page: #f5f5f5;
    --plum-deep: #2f2040;
    --plum: #4a3257;
    --plum-mid: #6c4f78;
    --mauve: #9a7c9f;
    --blush: #fbd6e4;
    --blush-soft: #f3e3ee;
    --ink: #2b1f33;
    --white: #ffffff;
    --headline: "Roboto Serif", Georgia, serif;
    --body: "Roboto", Arial, sans-serif;
  }
  * { box-sizing: border-box; margin: 0; padding: 0; }
  html, body { width: 1200px; height: 1122px; overflow: hidden; background: var(--page); }
  .board { position: relative; width: 1200px; height: 1122px; }

  .card { position: absolute; width: 259px; height: 324px; overflow: hidden; background: var(--plum); }
  .photo, .shade, .art { position: absolute; }
  .photo { inset: 0; }
  .copy { position: absolute; left: 14px; right: 14px; }
  .headline { font-family: var(--headline); font-weight: 800; color: var(--blush); line-height: 1.05; letter-spacing: -0.2px; }
  .headline em { font-style: italic; }
  .tagline { font-family: var(--body); font-size: 12px; line-height: 1.35; color: var(--blush-soft); margin-top: 10px; }
  .tagline em { font-style: italic; }
  .center { text-align: center; }
  .right { text-align: right; }
  .dark-tag { color: var(--ink); }

  /* photo tones */
  .tone-portrait { background: linear-gradient(160deg, #a98f83 0%, #6b4b48 35%, #2c2230 70%); }
  .tone-hug { background: linear-gradient(150deg, #c9a2b8 0%, #8a5a7e 40%, #b34d8e 70%, #d9e6a8 100%); }
  .tone-duo { background: linear-gradient(160deg, #c8a7a8 0%, #6d5a78 40%, #3e4a6e 75%); }
  .tone-studio { background: linear-gradient(180deg, #ffffff 0%, #e9e4ea 30%, #4a3b4f 60%); }

  .shade-bottom { inset: 0; background: linear-gradient(180deg, rgba(74,50,87,0) 35%, rgba(60,40,72,0.85) 62%, var(--plum) 100%); }
  .shade-full { inset: 0; background: rgba(88,62,102,0.6); }
  .shade-top-to-white { inset: 0; background: linear-gradient(180deg, var(--plum) 0%, var(--plum-mid) 28%, #c9bccd 52%, var(--white) 70%); }
  .shade-left { inset: 0; background: linear-gradient(90deg, rgba(70,48,84,0.95) 0%, rgba(70,48,84,0.7) 55%, rgba(70,48,84,0.1) 100%); }
</style>
</head>
<body>
<main class="board">

  <!-- Row 1 -->
  <article class="card" style="left:39px; top:46px;">
    <div class="photo tone-portrait" role="img" aria-label="Photo of RT smiling in a black top, hand on hip"></div>
    <div class="shade shade-bottom"></div>
    <div class="copy" style="bottom:10px;">
      <h2 class="headline" style="font-size:24px;">Stop Starting<br>Over<em>Every</em><br><em>Monday</em></h2>
      <p class="tagline">Stay Consistent with<br>RT in Your Pocket!</p>
    </div>
  </article>

  <article class="card" style="left:327px; top:46px;">
    <div class="photo tone-hug" role="img" aria-label="Photo of two women hugging in a store"></div>
    <div class="shade shade-full" style="background:linear-gradient(180deg, rgba(74,50,87,0.9) 0%, rgba(110,80,120,0.6) 45%, rgba(110,80,120,0.25) 100%);"></div>
    <div class="copy center" style="top:14px; left:8px; right:8px;">
      <h2 class="headline" style="font-size:24px;">You Don't Need more Willpower. You Need More <em>Support</em></h2>
      <p class="tagline" style="font-size:11.5px;">Stay Consistent with RT in Your Pocket!</p>
    </div>
  </article>

  <article class="card" style="left:615px; top:46px;">
    <div class="photo tone-duo" role="img" aria-label="Photo of RT and a friend laughing together"></div>
    <div class="shade shade-full"></div>
    <div class="copy center" style="top:139px; left:8px; right:8px;">
      <h2 class="headline" style="font-size:21px; text-transform:uppercase;">Built for <em>women</em> who are tired of doing this alone</h2>
      <p class="tagline" style="font-size:11.5px;">Stay Consistent with<br><em>RT in Your Pocket!</em></p>
    </div>
  </article>

  <article class="card" style="left:903px; top:46px;">
    <div class="photo tone-studio" role="img" aria-label="Photo of RT smiling against a white studio backdrop"></div>
    <div class="shade shade-bottom" style="background:linear-gradient(180deg, rgba(74,50,87,0) 40%, rgba(70,48,84,0.9) 60%, var(--plum) 100%);"></div>
    <div class="copy center" style="top:163px; left:6px; right:6px;">
      <h2 class="headline" style="font-size:27px;">When Motvation Fades, <em>RT Checks In</em></h2>
      <p class="tagline" style="font-size:14px; margin-top:14px;">Stay Consistent with<br><em>RT in You Pocket!</em></p>
    </div>
  </article>

  <!-- Row 2 -->
  <article class="card" style="left:39px; top:400px;">
    <div class="photo tone-hug" role="img" aria-label="Photo of RT hugging a friend in a store"></div>
    <div class="shade shade-bottom"></div>
    <div class="copy center" style="bottom:14px; left:8px; right:8px;">
      <h2 class="headline" style="font-size:26px;">The Support System You've Been <em>Missing</em></h2>
      <p class="tagline" style="font-size:14px;">Stay Consistent with<br><em>RT in You Pocket!</em></p>
    </div>
  </article>

  <article class="card" style="left:327px; top:400px;">
    <div class="photo tone-duo" role="img" aria-label="Photo of RT and a friend laughing side by side"></div>
    <div class="shade shade-bottom" style="background:linear-gradient(180deg, rgba(74,50,87,0) 40%, rgba(74,50,87,0.55) 100%);"></div>
    <div class="copy right" style="bottom:16px;">
      <h2 class="headline" style="font-size:27px;">What if<br>RT Checked<br>in <em>Every</em><br><em>Day?</em></h2>
      <p class="tagline" style="font-size:14px;">Stay Consistent with<br><em>RT in You Pocket!</em></p>
    </div>
  </article>

  <article class="card" style="left:618px; top:400px;">
    <div class="photo shade-top-to-white"></div>
    <div class="art" role="img" aria-label="Illustration of two women studying together at a desk with a laptop" style="left:0; right:0; bottom:0; height:165px; background:linear-gradient(180deg, rgba(255,255,255,0) 0%, #f0c6dc 45%, #c9a0e6 100%);"></div>
    <div class="copy" style="top:16px; left:24px;">
      <h2 class="headline" style="font-size:28px;">Support When <em>Motivation</em> Disappears</h2>
      <p class="tagline dark-tag" style="font-size:14px;">Stay Consistent with<br><em>RT in You Pocket!</em></p>
    </div>
  </article>

  <article class="card" style="left:903px; top:400px;">
    <div class="photo tone-portrait" role="img" aria-label="Photo of RT leaning on a counter, smiling"></div>
    <div class="shade shade-left"></div>
    <div class="copy" style="top:44px;">
      <h2 class="headline" style="font-size:30px; line-height:1.1;">The<br>Missing<br>Piece Isn't<br>Another<br><em>Diet</em></h2>
      <p class="tagline" style="font-size:14px; margin-top:28px;">Stay Consistent<br>with <em>RT in You<br>Pocket!</em></p>
    </div>
  </article>

  <!-- Row 3 -->
  <article class="card" style="left:325px; top:752px;">
    <div class="photo shade-top-to-white" style="background:linear-gradient(180deg, var(--plum) 0%, var(--plum-mid) 35%, #c9bccd 62%, var(--white) 78%);"></div>
    <div class="art" role="img" aria-label="Illustration of a woman turning away from a tray of burgers and fries" style="left:0; right:0; bottom:0; height:75px; background:linear-gradient(90deg, #f6d9e2 0%, rgba(255,255,255,0) 45%, rgba(255,255,255,0) 70%, #f4c9a8 100%);"></div>
    <div class="copy center" style="top:26px; left:8px; right:8px;">
      <h2 class="headline" style="font-size:34px;">One Bad Meal Doesn't Mean You <em>Failed</em></h2>
      <p class="tagline dark-tag" style="font-size:15.5px; margin-top:30px;">Stay Consistent with<br><em>RT in You Pocket!</em></p>
    </div>
  </article>

  <article class="card" style="left:616px; top:752px;">
    <div class="photo shade-top-to-white" style="background:linear-gradient(180deg, var(--plum) 0%, var(--plum-mid) 25%, #c4b5c8 50%, var(--white) 72%);"></div>
    <div class="art" role="img" aria-label="Illustration of hands holding a plate of fresh salad" style="right:0; top:0; width:110px; height:80px; background:radial-gradient(circle at 55% 40%, #e6d86a 0%, #b8a04e 45%, rgba(74,50,87,0) 70%);"></div>
    <div class="art" role="img" aria-label="Illustration of a woman jumping joyfully" style="right:0; bottom:0; width:82px; height:150px; background:linear-gradient(180deg, rgba(255,255,255,0) 0%, #f3a27e 35%, #4a6fb5 70%, rgba(255,255,255,0) 100%);"></div>
    <div class="copy" style="top:52px; left:17px; right:6px;">
      <h2 class="headline" style="font-size:29px;">Eat the Food You Love. <span style="color:var(--plum-deep);">Stay Accountable <em>Every Day.</em></span></h2>
      <p class="tagline dark-tag" style="font-size:15.5px; margin-top:36px;">Stay Consistent with<br>RT in You Pocket!</p>
    </div>
  </article>

</main>
</body>
</html>
```